The Linen Loft Co

We need a business card design for our wardrobe company.
Please visit our website www.gentlelinenlofts.com to get an idea of who we are.

```html
<!DOCTYPE html>
<html lang="en">
<head>
<meta charset="utf-8">
<title>The Linen Loft Co – Business Card</title>
<link rel="stylesheet" href="https://fonts.googleapis.com/css2?family=Open+Sans:wght@400;600;700&display=swap">
<style>
  :root {
    --backdrop: #e4e4e4;
    --card-white: #ffffff;
    --card-black: #050505;
    --ink: #111111;
    --ink-soft: #333333;
    --paper-text: #ffffff;
  }
  * { box-sizing: border-box; margin: 0; padding: 0; }
  html, body {
    width: 1200px; height: 900px; overflow: hidden;
    background: var(--backdrop);
    font-family: "Open Sans", Arial, sans-serif;
  }
  .stage {
    position: relative; width: 1200px; height: 900px;
    display: flex; align-items: center; justify-content: center; gap: 60px;
  }
  .card {
    position: relative; width: 525px; height: 300px;
    box-shadow: 0 6px 18px rgba(0,0,0,.18);
  }
  .card--front { background: var(--card-white); color: var(--ink); }
  .card--back { background: var(--card-black); color: var(--paper-text); }

  .holder { position: absolute; left: 36px; top: 38px; }
  .holder__name { font-size: 21px; font-weight: 700; letter-spacing: .5px; line-height: 1.1; }
  .holder__title { font-size: 14px; color: var(--ink-soft); margin-top: 2px; }

  .divider {
    position: absolute; left: 32px; right: 40px; top: 112px;
    height: 1.5px; background: var(--ink);
  }

  .contacts { position: absolute; left: 28px; top: 128px; list-style: none; }
  .contacts li {
    display: flex; align-items: center; gap: 10px;
    font-size: 15px; line-height: 23px; color: var(--ink-soft);
  }
  .contacts svg { width: 13px; height: 13px; flex: none; }

  .brand { display: flex; align-items: center; gap: 12px; }
  .brand__mark { width: 16px; height: 16px; flex: none; }
  .brand__name { font-size: 12.5px; font-weight: 600; letter-spacing: .6px; text-transform: uppercase; line-height: 1.2; white-space: nowrap; }
  .brand__tagline { font-size: 12.5px; font-weight: 600; line-height: 1.3; white-space: nowrap; }

  .card--front .brand { position: absolute; right: 44px; top: 40px; }
  .card--front .brand__mark { background: var(--ink); }

  .address {
    position: absolute; right: 44px; bottom: 30px;
    font-size: 15px; line-height: 20px; color: var(--ink-soft); text-align: left;
  }

  .card--back .brand { position: absolute; left: 50%; top: 50%; transform: translate(-50%, -50%); gap: 14px; }
  .card--back .brand__mark { background: var(--paper-text); width: 20px; height: 20px; }
  .card--back .brand__name, .card--back .brand__tagline { font-size: 14px; }
</style>
</head>
<body>
<main class="stage">
  <section class="card card--front" aria-label="Business card front">
    <div class="holder">
      <p class="holder__name">YOUR NAME</p>
      <p class="holder__title">Your Title</p>
    </div>

    <div class="brand">
      <span class="brand__mark" aria-hidden="true"></span>
      <div>
        <p class="brand__name">The Linen Loft Co</p>
        <p class="brand__tagline">Storage Made to Fit</p>
      </div>
    </div>

    <div class="divider"></div>

    <ul class="contacts">
      <li>
        <svg viewBox="0 0 16 16" aria-hidden="true"><path fill="#111" d="M3.6 1.2 6 3.8 4.8 5.6c.9 2 2.6 3.7 4.6 4.6l1.8-1.2 2.6 2.4-1.4 2.8C6.8 14 2 9.2 1 3z"/></svg>
        <span>123-456-2100</span>
      </li>
      <li>
        <svg viewBox="0 0 16 16" aria-hidden="true"><rect x="1" y="3" width="14" height="10" fill="#111"/><path d="M1.5 3.5 8 9l6.5-5.5" stroke="#fff" stroke-width="1.2" fill="none"/></svg>
        <span>youremail@example.com</span>
      </li>
      <li>
        <svg viewBox="0 0 16 16" aria-hidden="true"><circle cx="8" cy="8" r="7" fill="#111"/><path d="M1 8h14M8 1c-3 3.5-3 10.5 0 14M8 1c3 3.5 3 10.5 0 14" stroke="#fff" stroke-width="1" fill="none"/></svg>
        <span>www.gentlelinenlofts.com</span>
      </li>
    </ul>

    <p class="address">Your address, city<br>state, ZIP 0000</p>
  </section>

  <section class="card card--back" aria-label="Business card back">
    <div class="brand">
      <span class="brand__mark" aria-hidden="true"></span>
      <div>
        <p class="brand__name">The Linen Loft Co</p>
        <p class="brand__tagline">Storage Made to Fit</p>
      </div>
    </div>
  </section>
</main>
</body>
</html>
```